VKT Consulting

Government/Entitlement Consulting Services- I assist developers obtain entitlements from local, state and federal government agencies so that they can build their projects. Often these projects are very complicated and political and may face community opposition.

Target Market(s)

Real Estate Developers

Industry/Entity Type

Business Consultant

Contact Information for Business Card

Dana Melbrook
Principal

Font styles to use
Serif
Sans Serif

Requirements
Must have
• Classy and professional appeal.
Nice to have
• I like a combination of a mat and glossy finish. I've seen that done with black and then a bold color for a pop, but am not 100% committed to that.

```html
<!DOCTYPE html>
<html lang="en">
<head>
<meta charset="utf-8">
<title>VKT Consulting – Business Card</title>
<link href="https://fonts.googleapis.com/css2?family=Arimo:wght@400;700&display=swap" rel="stylesheet">
<style>
  :root {
    --bg: #e9e6e1;
    --card-black: #0d0d0d;
    --card-grey: #4a4546;
    --panel: #1a1a1a;
    --bar: #161616;
    --icon-bg: #f2f2f2;
    --text-light: #f4f4f4;
    --text-soft: #d9d9d9;
    --dash: #9a9a9a;
  }
  * { margin: 0; padding: 0; box-sizing: border-box; }
  html, body {
    width: 1200px; height: 892px; overflow: hidden;
    background: var(--bg);
    font-family: "Arimo", Arial, sans-serif;
  }
  .canvas {
    position: relative; width: 1200px; height: 892px;
    display: flex; align-items: center; justify-content: center; gap: 50px;
  }
  .card {
    position: relative; width: 525px; height: 300px;
    border-radius: 3px; overflow: hidden;
    box-shadow: 0 10px 28px rgba(0,0,0,.25);
  }
  /* Front */
  .card-front {
    background: radial-gradient(ellipse at 60% 40%, #1d1d1d 0%, var(--card-black) 70%);
    display: flex; align-items: center; justify-content: center;
  }
  .front-name {
    color: var(--text-light); font-weight: 700; font-size: 48px; letter-spacing: -0.5px;
  }
  /* Back */
  .card-back {
    background: linear-gradient(160deg, #554f50 0%, var(--card-grey) 55%, #3e3a3b 100%);
  }
  .brand-panel {
    position: absolute; left: 0; top: 0; width: 225px; height: 175px;
    background: linear-gradient(150deg, #222 0%, var(--panel) 60%, #111 100%);
    display: flex; align-items: center; justify-content: center;
  }
  .brand-panel::before, .brand-panel::after {
    content: ""; position: absolute; left: 0; right: 0;
    border-top: 1px dashed var(--dash);
  }
  .brand-panel::before { top: 8px; }
  .brand-panel::after { bottom: 8px; }
  .brand-name { color: var(--text-light); font-weight: 700; font-size: 22px; letter-spacing: -0.3px; }
  .person {
    position: absolute; left: 262px; top: 34px;
    display: flex; align-items: center; gap: 12px;
  }
  .person-icon { width: 34px; height: 34px; }
  .person-name { color: var(--text-light); font-size: 22px; line-height: 1.05; }
  .person-role { color: var(--text-soft); font-size: 15px; }
  .contact-list { position: absolute; left: 150px; top: 180px; list-style: none; }
  .contact-row {
    position: relative; display: flex; align-items: flex-start; gap: 14px;
    height: 30px; margin-bottom: 6px;
    width: 360px; background: var(--bar); border-radius: 5px; padding: 4px 6px;
  }
  .contact-row:nth-child(1) { margin-left: 40px; }
  .contact-row:nth-child(2) { margin-left: 20px; }
  .contact-icon {
    flex: none; width: 24px; height: 22px; border-radius: 4px; background: var(--icon-bg);
    display: flex; align-items: center; justify-content: center;
  }
  .contact-text { color: var(--text-light); font-size: 10.5px; line-height: 1.25; padding-top: 1px; }
</style>
</head>
<body>
<main class="canvas">
  <section class="card card-front">
    <h1 class="front-name">VKT Consulting</h1>
  </section>

  <section class="card card-back">
    <div class="brand-panel"><span class="brand-name">VKT Consulting</span></div>

    <div class="person">
      <svg class="person-icon" viewBox="0 0 34 34" aria-hidden="true">
        <circle cx="17" cy="17" r="17" fill="#f2f2f2"/>
        <circle cx="17" cy="13" r="5.5" fill="#2a2a2a"/>
        <path d="M7 27c1.5-5.5 5.5-8 10-8s8.5 2.5 10 8z" fill="#2a2a2a"/>
      </svg>
      <div>
        <div class="person-name">Dana Melbrook</div>
        <div class="person-role">Principal</div>
      </div>
    </div>

    <ul class="contact-list">
      <li class="contact-row">
        <span class="contact-icon">
          <svg width="14" height="14" viewBox="0 0 14 14" aria-hidden="true"><text x="7" y="11" text-anchor="middle" font-size="12" font-family="Arimo, sans-serif" font-weight="700" fill="#222">@</text></svg>
        </span>
        <span class="contact-text">www.vktconsulting.com<br>info@vktconsulting.com</span>
      </li>
      <li class="contact-row">
        <span class="contact-icon">
          <svg width="10" height="15" viewBox="0 0 10 15" aria-hidden="true"><rect x="0.5" y="0.5" width="9" height="14" rx="1.5" fill="#222"/><rect x="2" y="2" width="6" height="5" fill="#f2f2f2"/><g fill="#f2f2f2"><rect x="2" y="8.5" width="1.5" height="1.2"/><rect x="4.25" y="8.5" width="1.5" height="1.2"/><rect x="6.5" y="8.5" width="1.5" height="1.2"/><rect x="2" y="10.7" width="1.5" height="1.2"/><rect x="4.25" y="10.7" width="1.5" height="1.2"/><rect x="6.5" y="10.7" width="1.5" height="1.2"/></g></svg>
        </span>
        <span class="contact-text">512-555-0147</span>
      </li>
      <li class="contact-row">
        <span class="contact-icon">
          <svg width="16" height="14" viewBox="0 0 16 14" aria-hidden="true"><path d="M8 1 1 7h2v6h4V9h2v4h4V7h2z" fill="#222"/></svg>
        </span>
        <span class="contact-text">14 Harlow Lane Kingsford<br>NSW 2032</span>
      </li>
    </ul>
  </section>
</main>
</body>
</html>
```